Solar Company Bussiness Card

I need a 2 sided business card and would like a .psd and any font files for each side of the card. I would like my logo used, it should be attached with the fonts. I'm not opposed to the font colors with the logo being changed.

On the sample design, I'd like the following:

Marcus Dellow
President
Phone: 555-382-9174
www.brightvanepower.example

As I've recently opened in a 2nd market, I'm not sure about an address as I currently have 2 of them. I may actually get separate cards printed, one batch for each address, that's why I need the PSD file.
Updates

I'm very pleased with the response and designs I've received here for my business card. First and foremost, I'd like to thank everyone who took the time to submit a design. There truly are a lot of great designs in the bunch here and I'm having a little difficulty deciding. I will be reaching out to someone in the next day or two here to go to a final design. At this time, I'm not looking for any new concepts. If any of you do logos, I'm looking for a new logo for our sister entity, Dellow Partners, Inc. Thanks, Marcus Dellow

Reason: I'm not looking for any new designs at this point, but extending this deadline in order to give people I've asked a chance to re-submit items.

Industry/Entity Type

Business

```html
<!DOCTYPE html>
<html lang="en">
<head>
<meta charset="utf-8">
<title>Brightvane Power – Business Card</title>
<link rel="stylesheet" href="https://fonts.googleapis.com/css2?family=Exo+2:wght@400;500;600&display=swap">
<style>
  :root {
    --page-bg: #e6e7e9;
    --card-white: #ffffff;
    --card-shade: #eef0f2;
    --blue-light: #13a9ec;
    --blue-mid: #1b82d8;
    --blue-deep: #2253b8;
    --swoosh-dark: #2a2a2e;
    --swoosh-light: #9a9ca0;
    --brand-blue: #1a5aa6;
    --text-white: #ffffff;
  }
  * { box-sizing: border-box; margin: 0; padding: 0; }
  html, body {
    width: 1200px; height: 900px; overflow: hidden;
    background: var(--page-bg);
    font-family: "Exo 2", "Segoe UI", sans-serif;
  }
  .canvas {
    width: 1200px; height: 900px;
    display: flex; align-items: center; justify-content: center;
  }
  .business-card {
    position: relative;
    width: 1050px; height: 600px;
    background: linear-gradient(160deg, var(--card-white) 40%, var(--card-shade));
    box-shadow: 0 10px 30px rgba(0,0,0,0.15);
    overflow: hidden;
  }
  .card-art { position: absolute; inset: 0; }
  .brand {
    position: absolute; left: 70px; top: 300px;
    display: flex; align-items: center; gap: 18px;
    color: var(--brand-blue);
  }
  .brand-square {
    width: 46px; height: 46px; background: var(--brand-blue);
  }
  .brand-name {
    font-size: 50px; font-weight: 500; letter-spacing: 0.5px;
  }
  .contact-block {
    position: absolute; right: 40px; top: 48px;
    text-align: right; color: var(--text-white);
  }
  .person-name {
    font-size: 36px; font-weight: 600; letter-spacing: 3px; text-transform: uppercase;
  }
  .person-title { font-size: 22px; font-weight: 400; margin-top: 2px; }
  .address { font-size: 25px; line-height: 1.25; margin-top: 48px; }
  .contact-list { list-style: none; margin-top: 44px; }
  .contact-list li {
    display: flex; align-items: center; justify-content: flex-end; gap: 14px;
    font-size: 22px; line-height: 1.65;
  }
  .contact-list svg { width: 22px; height: 22px; flex: none; }
  .contact-list .no-icon { padding-right: 36px; }
</style>
</head>
<body>
<main class="canvas">
  <section class="business-card">
    <svg class="card-art" viewBox="0 0 1050 600" preserveAspectRatio="none" aria-hidden="true">
      <defs>
        <radialGradient id="blueField" cx="68%" cy="45%" r="60%">
          <stop offset="0" stop-color="var(--blue-light)"/>
          <stop offset="0.55" stop-color="var(--blue-mid)"/>
          <stop offset="1" stop-color="var(--blue-deep)"/>
        </radialGradient>
        <linearGradient id="swooshTone" x1="0" y1="0" x2="0" y2="1">
          <stop offset="0" stop-color="var(--swoosh-light)"/>
          <stop offset="1" stop-color="var(--swoosh-dark)"/>
        </linearGradient>
      </defs>
      <path class="blue-panel" d="M500 0 H1050 V600 H610 C650 420 610 190 500 0 Z" fill="url(#blueField)"/>
      <path class="swoosh-band" d="M500 0 C610 190 650 420 610 600 H596 C610 520 600 420 560 300 C535 210 510 110 470 0 Z" fill="url(#swooshTone)"/>
      <path class="swoosh-gap" d="M470 0 C510 110 535 210 560 300 C600 420 610 520 596 600 H584 C596 520 586 420 546 300 C520 210 495 110 458 0 Z" fill="#ffffff"/>
    </svg>

    <div class="brand">
      <span class="brand-square"></span>
      <span class="brand-name">Brightvane Power</span>
    </div>

    <div class="contact-block">
      <h1 class="person-name">Owen Hartley</h1>
      <p class="person-title">Managing Director</p>
      <p class="address">047,12th floor,Park<br>Meridian Road TRV</p>
      <ul class="contact-list">
        <li>012 555 0142
          <svg viewBox="0 0 24 24"><path d="M6 3l3 0 2 5-2 2c1 2 3 4 5 5l2-2 5 2v3c0 1-1 2-2 2C10 20 4 14 4 5c0-1 1-2 2-2z" fill="#fff"/></svg>
        </li>
        <li>012 555 0142
          <svg viewBox="0 0 24 24"><rect x="6" y="2" width="12" height="20" rx="2" fill="none" stroke="#fff" stroke-width="2"/><circle cx="12" cy="18" r="1.3" fill="#fff"/></svg>
        </li>
        <li>012 555 0142
          <svg viewBox="0 0 24 24"><rect x="5" y="9" width="14" height="11" fill="#fff"/><rect x="8" y="3" width="8" height="6" fill="none" stroke="#fff" stroke-width="2"/></svg>
        </li>
        <li>yourname@mailbox.example
          <svg viewBox="0 0 24 24"><rect x="2" y="5" width="20" height="14" fill="#fff"/><path d="M2 5l10 8 10-8" fill="none" stroke="#1b82d8" stroke-width="1.6"/></svg>
        </li>
        <li>www.yourwebsite.example
          <svg viewBox="0 0 24 24"><circle cx="12" cy="12" r="9" fill="none" stroke="#fff" stroke-width="2"/><path d="M3 12h18M12 3c-4 5-4 13 0 18M12 3c4 5 4 13 0 18" fill="none" stroke="#fff" stroke-width="1.5"/></svg>
        </li>
      </ul>
    </div>
  </section>
</main>
</body>
</html>
```